South Florida Real Estate Brokerage Business

The name is LAKE VORISSA REAL ESTATE.
The company is a Real estate realty based in Miami.
Is targeted to Latin American clients.
Must express luxury, and efficiency.
Target clients for properties around 250k to a million +.
Vorissa means Royal in Latin.
Should communicate safety and knowledge of the product and transaction with a tech edge.

The web design needs to be a Social tool, with Friendloop and other media integration of some sort. Needs to have a Show case place, a Search place (MLS listings) with maps and filters.
Needs to reflect luxury but also mixed with a social edge capable of engaging clients or transition them to communicate with the page.
Include the logo from the uploaded files, feel free to change the color or font per webdesign.
This is a Front en design, layout and graphics.
Possible future programming if approved.
I can receive Quotes for the Code part.

Spanish and English speakers living in Latin America and Canada looking for apartments and houses to buy.

Business

• Search area.
Neighbourhood area.
Could be a blog or news area.
Client registration.
Social Plugin
• Social linking to networks.
Log in with friendloop account.
Friendloop Like.

```html
<!DOCTYPE html>
<html lang="en">
<head>
<meta charset="utf-8">
<title>Lake Vorissa Real Estate</title>
<link href="https://fonts.googleapis.com/css2?family=Cinzel:wght@400;600&family=Open+Sans:wght@400;600;700&family=Questrial&display=swap" rel="stylesheet">
<style>
:root{
  --header-dark:#1c1817;
  --header-mid:#2e2826;
  --gold:#d2b06a;
  --gold-soft:#c9a96a;
  --gold-light:#e8cf94;
  --ink:#1e1e1e;
  --text:#3a3a3a;
  --muted:#8a827d;
  --accent:#b8772a;
  --footer-head:#e0612a;
  --footer-text:#a9a09a;
  --line:#dcdcdc;
  --friend-blue:#3b5998;
  --friend-border:#b3c1d9;
  --green-top:#78d552;
  --green-bottom:#2f9a1f;
  --beige:#cfc2ad;
  --panel:#efefef;
}
*{box-sizing:border-box;margin:0;padding:0}
html,body{width:889px;height:1200px;overflow:hidden;background:#fff}
body{position:relative;font-family:"Open Sans",Arial,sans-serif;color:var(--text)}
.abs{position:absolute}

/* Header */
.site-header{position:absolute;left:0;top:0;width:889px;height:116px;background:linear-gradient(180deg,var(--header-mid),var(--header-dark))}
.brand{position:absolute;left:100px;top:70px;width:164px;text-align:center;font-family:"Cinzel",serif;color:var(--gold-soft);font-weight:400;line-height:1}
.brand-name{font-size:20px;letter-spacing:.3px;display:block}
.brand-sub{font-size:12px;letter-spacing:1px;display:block;margin-top:5px}
.login label{position:absolute;font-size:8.5px;color:var(--gold-light)}
.login .field{position:absolute;height:20px;background:#141110;border:1px solid #2b2523}
.login .btn-login{position:absolute;left:745px;top:20px;width:40px;height:20px;background:linear-gradient(#e3c47f,#c9a25a);color:#2a2220;font-size:10px;font-weight:600;text-align:center;line-height:20px}
.login .check{position:absolute;left:443px;top:46px;width:10px;height:10px;background:#141110;border:1px solid #3a3331}
.login .small{position:absolute;top:46px;font-size:8.5px;color:var(--gold)}
.main-nav{position:absolute;left:291px;top:94px;display:flex;font-size:9px;color:var(--gold);letter-spacing:0}
.main-nav span{padding:0 13px;border-left:1px solid #4a4240;line-height:12px}
.main-nav span:first-child{padding-left:0;border-left:0;color:#fff}
.main-nav span:last-child{padding-right:0}

/* Hero slider */
.hero{position:absolute;left:104px;top:123px;width:681px;height:297px;background:#2a2523}
.hero-image{position:absolute;left:7px;top:7px;width:667px;height:283px;border-radius:24px;background:linear-gradient(180deg,#d7e3ee 0%,#b9c6d6 30%,#9aa3ad 52%,#6f8a4d 72%,#4f7a2a 100%)}
.hero-arrow{position:absolute;top:129px}

/* Welcome */
.welcome-head{position:absolute;left:104px;top:434px;width:336px;height:27px;background:linear-gradient(90deg,#c9a25a 0%,#e2c588 45%,rgba(255,255,255,0) 100%);border-left:6px solid #2a2523;font-family:"Cinzel",serif;font-weight:400;font-size:17px;color:var(--ink);padding-left:8px;line-height:28px;letter-spacing:.3px}
.welcome-copy{position:absolute;left:104px;top:467px;width:336px;font-size:8.3px;line-height:12.2px;color:var(--text)}
.welcome-copy p+p{margin-top:12px}
.read-more{position:absolute;left:388px;top:562px;font-size:8.5px;color:var(--accent)}

/* Property search */
.search-box{position:absolute;left:462px;top:433px;width:323px;height:139px;border:1px solid #d8d8d8;background:#fff}
.tabs{display:flex;height:29px;background:#2a2523}
.tabs span{font-family:"Cinzel",serif;font-size:9.5px;color:var(--gold);line-height:29px;text-align:center;border-left:1px solid #4a4240}
.tabs .active{background:#fff;color:var(--ink);font-weight:600;border-left:0}
.search-box .lbl{position:absolute;font-size:8.5px;color:var(--text)}
.radio{position:absolute;width:9px;height:9px;border-radius:50%;border:1px solid #999;background:#fff}
.radio.on::after{content:"";position:absolute;left:2px;top:2px;width:3px;height:3px;border-radius:50%;background:#2b63b5}
.select{position:absolute;height:13px;border:1px solid #aaa;background:#fff;font-size:7px;line-height:11px;padding-left:3px;color:#222}
.select::after{content:"▾";position:absolute;right:3px;top:0;font-size:7px}
.btn-search{position:absolute;left:200px;top:105px;width:107px;height:20px;background:linear-gradient(var(--green-top),var(--green-bottom));border:1px solid #2a7d18;font-size:9.5px;text-align:center;line-height:18px;color:#e8f59e;letter-spacing:.3px}

.divider{position:absolute;left:104px;top:585px;width:681px;height:1px;background:linear-gradient(90deg,#fff,#e4e4e4 20%,#e4e4e4 80%,#fff)}

/* News */
.section-title{position:absolute;font-family:"Questrial",sans-serif;font-weight:400;color:var(--ink)}
.news-item{position:absolute;left:105px;width:430px}
.cal{position:absolute;left:0;top:0;width:42px;height:40px;border-radius:3px;background:#f1f1f1;border:1px solid #cfcfcf;text-align:center;overflow:hidden}
.cal .month{display:block;height:13px;background:#d9782a;color:#fff;font-size:6.5px;font-weight:700;line-height:13px}
.cal .day{display:block;font-family:"Cinzel",serif;font-size:15px;color:#222;line-height:24px;font-weight:600}
.news-item h3{position:absolute;left:58px;top:1px;font-size:9.8px;font-weight:600;color:#111;white-space:nowrap}
.news-item p{position:absolute;left:58px;top:19px;width:352px;font-size:8.5px;line-height:12.5px;color:#444}
.news-more{position:absolute;left:104px;top:751px;width:429px;height:18px;background:#e6e6e6;font-size:7.5px;color:#333;text-align:right;padding-right:14px;line-height:18px}

/* Social plugin */
.social-box{position:absolute;left:604px;top:600px;width:181px;height:170px;border:1px solid var(--friend-border);background:#fff;font-size:7px;color:#333}
.social-box .page-mark{position:absolute;left:6px;top:6px;width:29px;height:29px;background:#2a2523}
.social-box .page-name{position:absolute;left:48px;top:9px;color:var(--friend-blue);font-weight:700}
.social-box .page-name b{color:#333;font-weight:400}
.btn-like{position:absolute;left:43px;top:23px;width:31px;height:15px;border:1px solid #9aa9c8;background:#eef1f7;font-size:7px;line-height:13px;text-align:center;color:#333}
.btn-signup{position:absolute;left:129px;top:20px;width:43px;height:18px;background:#5bab45;border:1px solid #3f8a2d;color:#fff;font-size:8px;font-weight:700;text-align:center;line-height:16px}
.social-box .fans-count{position:absolute;left:6px;top:48px}
.fan{position:absolute;width:28px;text-align:left}
.fan .avatar{display:block;width:28px;height:28px}
.fan .nm{display:block;margin-top:2px;font-size:7px}
.social-box .plugin-foot{position:absolute;left:6px;right:6px;top:152px;border-top:1px solid #ccc;padding-top:3px;font-size:6.5px;color:#666}
.plugin-foot i{display:inline-block;width:8px;height:8px;background:var(--friend-blue);vertical-align:-1px;margin-right:3px}

/* Gallery */
.gallery{position:absolute;left:104px;top:811px;width:681px;height:174px;background:var(--panel);border:1px solid #dcdcdc;border-radius:6px}
.gallery-inner{position:absolute;left:5px;top:20px;width:669px;height:148px;background:var(--beige);border-radius:4px;box-shadow:inset 0 0 10px rgba(0,0,0,.12)}
.gallery-cap{position:absolute;left:104px;top:789px;z-index:2}
.gallery-title{z-index:3;left:0;width:889px;text-align:center;top:802px;font-size:17px;letter-spacing:.5px;line-height:22px}
.thumb{position:absolute;top:33px;width:128px;height:124px;background:#f4f4f4;box-shadow:0 1px 3px rgba(0,0,0,.3)}
.thumb .photo{position:absolute;left:8px;top:7px;width:112px;height:110px}
.g-arrow{position:absolute;top:884px;z-index:2}

/* Footer */
.site-footer{position:absolute;left:0;top:1010px;width:889px;height:190px;background:radial-gradient(ellipse at 50% 30%,#3a3230 0%,#231e1c 70%)}
.foot-col{position:absolute;top:25px;font-size:7.8px;color:var(--footer-text);line-height:12.5px}
.foot-col h4{font-size:8px;font-weight:700;color:var(--footer-head);margin-bottom:6px;letter-spacing:.2px}
.foot-col .hot{color:var(--footer-head)}
.mail-field{position:absolute;left:0;top:64px;width:120px;height:18px;background:#fff;font-size:7px;color:#666;line-height:18px;padding-left:6px}
.mail-btn{position:absolute;left:120px;top:64px;width:40px;height:18px;background:#d4522a;color:#fff;font-size:8px;text-align:center;line-height:18px}
.blog-post{margin-bottom:12px}
.copyright{position:absolute;left:105px;top:1182px;font-size:7.8px;color:var(--footer-text)}
.social-links{position:absolute;left:736px;top:1180px;display:flex;gap:8px}
.social-links span{width:11px;height:11px;border-radius:2px}
</style>
</head>
<body>

<header class="site-header">
  <div class="brand">
    <span class="brand-name">LAKE VORISSA</span>
    <span class="brand-sub">REAL ESTATE</span>
  </div>

  <div class="login">
    <label style="left:443px;top:7px">User ID</label>
    <div class="field" style="left:443px;top:20px;width:145px"></div>
    <label style="left:593px;top:7px">Password</label>
    <div class="field" style="left:593px;top:20px;width:145px"></div>
    <div class="btn-login">Log in</div>
    <div class="check"></div>
    <span class="small" style="left:458px">Remember me</span>
    <span class="small" style="left:593px">Forgot your Password ? / Register</span>
  </div>

  <nav class="main-nav">
    <span>HOME</span><span>COMPANY</span><span>ASSOCIATES</span><span>SEARCH PROPERTIES</span><span>MARKETING &amp;DESIGN</span><span>CONTACT</span>
  </nav>
</header>

<section class="hero">
  <div class="hero-image" role="img" aria-label="Photo of a large grey two-storey family house with a porch, lawn and flowering garden"></div>
  <svg class="hero-arrow" style="left:11px" width="38" height="38" viewBox="0 0 38 38"><circle cx="19" cy="19" r="19" fill="#d2ae67"/><path d="M22 11 L14 19 L22 27" stroke="#2a2220" stroke-width="2.5" fill="none"/></svg>
  <svg class="hero-arrow" style="left:632px" width="38" height="38" viewBox="0 0 38 38"><circle cx="19" cy="19" r="19" fill="#d2ae67"/><path d="M16 11 L24 19 L16 27" stroke="#2a2220" stroke-width="2.5" fill="none"/></svg>
</section>

<h2 class="welcome-head">WELCOME TO LAKE VORISSA</h2>
<div class="welcome-copy">
  <p>Lorem Ipsum is simply dummy text of the printing and typesetting industry. Lorem Ipsum has been the industry's standard dummy text ever since the 1500s, when an unknown printer took a of type and scrambled it to make a type specimen book.</p>
  <p>Lorem Ipsum comes from sections 1.10.32 and 1.10.33 of "de Finibus Bonorum et Malorum" (The Extremes of Good and Evil) by Caelius Marro, written in 45 BC. This book is a treatise on the theory of ethics, very popular during the Renaissance.</p>
</div>
<span class="read-more">Read More →</span>

<section class="search-box">
  <div class="tabs">
    <span class="active" style="width:114px">PROPERTY SEARCH</span>
    <span style="width:122px">OPEN HOUSE SEARCH</span>
    <span style="width:86px">MAP SEARCH</span>
  </div>
  <span class="radio on" style="left:13px;top:42px"></span><span class="lbl" style="left:28px;top:41px">For Sale</span>
  <span class="radio" style="left:13px;top:65px"></span><span class="lbl" style="left:28px;top:64px">For Rent</span>
  <span class="lbl" style="left:112px;top:41px">Property Type</span><span class="select" style="left:174px;top:41px;width:71px">Condominiums</span>
  <span class="lbl" style="left:126px;top:63px">City Name</span><span class="select" style="left:174px;top:63px;width:71px">Miami Beach</span>
  <span class="lbl" style="left:13px;top:89px">Price Min</span><span class="select" style="left:55px;top:89px;width:54px">$250,000</span>
  <span class="lbl" style="left:13px;top:111px">Price Max</span><span class="select" style="left:55px;top:111px;width:54px">$5 M+</span>
  <span class="lbl" style="left:131px;top:89px">Beds</span><span class="select" style="left:155px;top:89px;width:25px">1+</span>
  <span class="lbl" style="left:129px;top:111px">Baths</span><span class="select" style="left:155px;top:111px;width:25px">1+</span>
  <div class="btn-search">PROPERTY SEARCH</div>
</section>

<div class="divider"></div>

<h2 class="section-title" style="left:104px;top:597px;font-size:15px">LATEST NEWS</h2>

<article class="news-item" style="top:625px">
  <div class="cal"><span class="month">AUG</span><span class="day">21</span></div>
  <h3>Lorem Ipsum is simply dummy text of the printing and type setting industry.</h3>
  <p>Lorem Ipsum is simply dummy text of the printing and typesetting industry. Lorem Ipsum has been the industry's standard dummy text ever since the 1500s...</p>
</article>
<article class="news-item" style="top:685px">
  <div class="cal"><span class="month">AUG</span><span class="day">21</span></div>
  <h3>Lorem Ipsum is simply dummy text of the printing and type setting industry.</h3>
  <p>Lorem Ipsum is simply dummy text of the printing and typesetting industry. Lorem Ipsum has been the industry's standard dummy text ever since the 1500s...</p>
</article>
<div class="news-more">view all news ›</div>

<aside class="social-box">
  <span class="page-mark"></span>
  <span class="page-name">Lake Vorissa <b>on Friendloop</b></span>
  <span class="btn-like">Like</span>
  <span class="btn-signup">Sign Up</span>
  <span class="fans-count">560 people like <b>Lake Vorissa</b></span>
  <span class="fan" style="left:6px;top:60px"><span class="avatar" role="img" aria-label="Profile photo" style="background:#d9a58a"></span><span class="nm">Stacey</span></span>
  <span class="fan" style="left:44px;top:60px"><span class="avatar" role="img" aria-label="Profile photo" style="background:#7d8a8f"></span><span class="nm">Murry</span></span>
  <span class="fan" style="left:82px;top:60px"><span class="avatar" role="img" aria-label="Profile photo" style="background:#5a4038"></span><span class="nm">Amanda</span></span>
  <span class="fan" style="left:120px;top:60px"><span class="avatar" role="img" aria-label="Profile photo" style="background:#8a6a5a"></span><span class="nm">Marie</span></span>
  <span class="fan" style="left:6px;top:110px"><span class="avatar" role="img" aria-label="Profile photo" style="background:#6a4a60"></span><span class="nm">Lisa</span></span>
  <span class="fan" style="left:44px;top:110px"><span class="avatar" role="img" aria-label="Profile photo" style="background:#6f7a50"></span><span class="nm">Brett</span></span>
  <span class="fan" style="left:82px;top:110px"><span class="avatar" role="img" aria-label="Profile photo" style="background:#b28a7a"></span><span class="nm">Rebecca</span></span>
  <span class="fan" style="left:120px;top:110px"><span class="avatar" role="img" aria-label="Profile photo" style="background:#c07a6a"></span><span class="nm">Zane</span></span>
  <div class="plugin-foot"><i></i>Friendloop social plugin</div>
</aside>

<section class="gallery">
  <div class="gallery-inner"></div>
  <div class="thumb" style="left:46px"><div class="photo" role="img" aria-label="Photo of a white modern apartment building" style="background:linear-gradient(180deg,#c9dcef,#e8e8e6 60%,#8da06a)"></div></div>
  <div class="thumb" style="left:199px"><div class="photo" role="img" aria-label="Photo of a high-rise apartment block under blue sky" style="background:linear-gradient(180deg,#3f7fc7,#9bb8d6 50%,#c9c9c9 80%,#7a9158)"></div></div>
  <div class="thumb" style="left:353px"><div class="photo" role="img" aria-label="Photo of a suburban family house with front lawn" style="background:linear-gradient(180deg,#d9e4ec,#9a9088 50%,#6f8d4a)"></div></div>
  <div class="thumb" style="left:507px"><div class="photo" role="img" aria-label="Photo of a large Victorian-style house with garden" style="background:linear-gradient(180deg,#e6eaec,#b7b7b0 50%,#5f8440)"></div></div>
</section>
<svg class="gallery-cap" width="681" height="30" viewBox="0 0 681 30">
  <path d="M0 23 Q120 23 200 6 Q340 -4 480 6 Q560 23 681 23 L681 30 L0 30 Z" fill="#efefef"/>
  <path d="M0 23 Q120 23 200 6 Q340 -4 480 6 Q560 23 681 23" fill="none" stroke="#dcdcdc"/>
</svg>
<h2 class="section-title gallery-title">PHOTO GALLERY</h2>
<svg class="g-arrow" style="left:104px" width="25" height="42" viewBox="0 0 25 42"><path d="M0 0 A21 21 0 0 1 0 42 Z" fill="#fff" stroke="#ccc"/><path d="M13 16 L8 21 L13 26 Z" fill="#333"/></svg>
<svg class="g-arrow" style="left:760px" width="25" height="42" viewBox="0 0 25 42"><path d="M25 0 A21 21 0 0 0 25 42 Z" fill="#fff" stroke="#ccc"/><path d="M12 16 L17 21 L12 26 Z" fill="#333"/></svg>

<footer class="site-footer">
  <div class="foot-col" style="left:105px">
    <h4>QUICK LINKS</h4>
    Home<br>Company<br>Associates<br>Search Properties<br>Marketing &amp;Design<br>Contact
  </div>
  <div class="foot-col" style="left:240px">
    <h4>CONTACT US</h4>
    <div style="padding-left:4px">012 Lorem Ipsum,<br>dummy text.<br>(000) 123-4567 Phone<br>(000) 123-4567 Fax<br><span class="hot">Email-info@lakevorissa.example</span></div>
  </div>
  <div class="foot-col" style="left:408px;width:165px">
    <h4>JOIN THE MAILING LIST</h4>
    Users avoid filling out forms and submitting their details if possible. For a newsletter sign-ups, all you need is their email address.
    <div class="mail-field">Enter Your E-mail...</div>
    <div class="mail-btn">Sign Up</div>
  </div>
  <div class="foot-col" style="left:615px">
    <h4>RECENT BLOG POST</h4>
    <div class="blog-post"><span class="hot">12 March, 2012</span><br>Lorem Ipsum is simply dummy text...</div>
    <div class="blog-post"><span class="hot">12 March, 2012</span><br>Lorem Ipsum is simply dummy text...</div>
    <div class="blog-post"><span class="hot">12 March, 2012</span><br>Lorem Ipsum is simply dummy text...</div>
  </div>
</footer>
<p class="copyright">© 2012 Lake Vorissa. | All Rights Reserved.</p>
<div class="social-links">
  <span style="background:#3b5998"></span>
  <span style="background:#4aa3df"></span>
  <span style="background:#2a74b0"></span>
</div>

</body>
</html>
```